We need a new business card that reflects who we are. Professional, classy, modern, and service ori

We need a business card design for a window coverings design company in Kansas City called Bright Lane Interiors. We offer professional, modern, and high quality window covering products. We are looking to portray an image of a big, national franchise. We are a 5 location (with showrooms) business with 10 professional designers and 4 professional installers. These cards will be used with Thank you cards, given to realtors, and asked for referrals with.

Target Market(s)

Kansas City

Industry/Entity Type

Business

Contact Information for Business Card

We would like our card to look clean and simple on the front, featuring our logo and Marlow Fenwick's. Our designers' phone numbers and emails should be displayed as well as their title.

Font styles to use
Sans Serif

Colors

Designer to choose colors to be used in the design.

Requirements
Must have
• Front - Logos, name, phone number, email address
• Back - Showroom locations, social media? Appt date/time?
Nice to have
• I would like a clean and modern look (not contemporary. I like a white background, but I am open to ideas. Looking for a "National chain" look for a small business.
Should not have
• Too much busyness.

```html
<!DOCTYPE html>
<html lang="en">
<head>
<meta charset="utf-8">
<title>Bright Lane Interiors – Business Card</title>
<link rel="stylesheet" href="https://fonts.googleapis.com/css2?family=Tinos:wght@400;700&family=Roboto:wght@400;500;700&display=swap">
<style>
  :root {
    --stage: #2b2b2d;
    --card: #ffffff;
    --band: #a6a8ab;
    --ink: #1d1d1d;
    --ink-soft: #5b5b5e;
    --rule: #9a9a9d;
    --accent-red: #c7434a;
    --accent-orange: #ef8a2c;
    --partner: #4a5d7e;
    --suffix: #6b3b3e;
    --social: #a3a3a6;
  }
  * { box-sizing: border-box; margin: 0; padding: 0; }
  html, body { width: 1200px; height: 900px; overflow: hidden; }
  body {
    background: var(--stage);
    display: flex;
    flex-direction: column;
    align-items: center;
    justify-content: center;
    gap: 36px;
    font-family: "Roboto", Arial, sans-serif;
  }
  .card {
    width: 700px;
    height: 400px;
    background: var(--card);
    position: relative;
    overflow: hidden;
    box-shadow: 0 10px 30px rgba(0,0,0,.45);
  }

  /* Front */
  .card-front {
    display: flex;
    flex-direction: column;
    align-items: center;
    justify-content: center;
  }
  .brand-mark { display: flex; align-items: center; gap: 14px; }
  .brand-square { width: 46px; height: 46px; background: var(--accent-red); }
  .brand-name {
    font-family: "Tinos", "Times New Roman", serif;
    font-size: 40px;
    color: var(--ink);
    font-weight: 400;
  }
  .brand-tagline {
    margin-top: 10px;
    font-family: "Tinos", "Times New Roman", serif;
    font-size: 19px;
    color: var(--ink);
  }

  /* Back */
  .contact-band {
    position: absolute;
    left: 0; top: 0;
    width: 100%; height: 168px;
    background: var(--band);
    display: flex;
    align-items: center;
    color: #fff;
    font-family: "Tinos", "Times New Roman", serif;
  }
  .designer {
    width: 300px;
    text-align: right;
    padding-right: 26px;
    border-right: 1px solid rgba(255,255,255,.8);
  }
  .designer-name { font-size: 24px; font-weight: 700; letter-spacing: .5px; }
  .designer-title { font-size: 17px; letter-spacing: 1px; }
  .contact-list {
    list-style: none;
    padding-left: 24px;
    display: flex;
    flex-direction: column;
    gap: 6px;
    font-size: 17px;
  }
  .contact-list li { display: flex; align-items: center; gap: 12px; }
  .contact-icon {
    width: 20px; height: 20px;
    background: #fff;
    display: flex; align-items: center; justify-content: center;
  }

  .appointment {
    position: absolute;
    left: 40px; top: 196px;
    width: 620px;
    font-size: 18px;
    color: var(--ink-soft);
  }
  .field-row { display: flex; align-items: flex-end; gap: 8px; height: 36px; }
  .field-line { flex: 1; border-bottom: 1px dotted var(--rule); height: 18px; }
  .field-line.short { flex: 0 0 150px; }
  .field-suffix { font-size: 13px; color: var(--suffix); }

  .partner {
    position: absolute;
    right: 40px; top: 290px;
    display: flex; align-items: center; gap: 8px;
    font-size: 16px; font-weight: 500;
    color: var(--partner);
  }
  .partner-dot { width: 16px; height: 16px; border-radius: 50%; background: var(--accent-orange); }

  .locations {
    position: absolute;
    left: 40px; top: 318px;
    font-size: 14px;
    font-weight: 700;
    color: var(--ink-soft);
    letter-spacing: .3px;
  }
  .social {
    position: absolute;
    left: 40px; bottom: 22px;
    display: flex; gap: 8px;
    list-style: none;
  }
  .social li { width: 22px; height: 22px; border-radius: 50%; background: var(--social); }
</style>
</head>
<body>

  <section class="card card-front" aria-label="Card front">
    <div class="brand-mark">
      <span class="brand-square"></span>
      <span class="brand-name">Bright Lane Interiors</span>
    </div>
    <p class="brand-tagline">Blinds, Shades, Shutters, Draperies &amp; Decor</p>
  </section>

  <section class="card card-back" aria-label="Card back">
    <div class="contact-band">
      <div class="designer">
        <p class="designer-name">ALEX MORGAN</p>
        <p class="designer-title">DESIGNER</p>
      </div>
      <ul class="contact-list">
        <li>
          <span class="contact-icon">
            <svg width="12" height="12" viewBox="0 0 24 24"><path fill="#a6a8ab" d="M6.6 10.8a15 15 0 0 0 6.6 6.6l2.2-2.2a1 1 0 0 1 1-.25 11.4 11.4 0 0 0 3.6.57 1 1 0 0 1 1 1V20a1 1 0 0 1-1 1A17 17 0 0 1 3 4a1 1 0 0 1 1-1h3.5a1 1 0 0 1 1 1c0 1.25.2 2.45.57 3.6a1 1 0 0 1-.25 1z"/></svg>
          </span>913.555.0148
        </li>
        <li>
          <span class="contact-icon">
            <svg width="12" height="12" viewBox="0 0 24 24"><rect x="2" y="5" width="20" height="14" fill="#a6a8ab"/><path d="M2 5l10 8 10-8" fill="none" stroke="#fff" stroke-width="2"/></svg>
          </span>info@brightlaneinteriors.com
        </li>
        <li>
          <span class="contact-icon">
            <svg width="12" height="12" viewBox="0 0 24 24"><circle cx="12" cy="12" r="9" fill="none" stroke="#a6a8ab" stroke-width="2.5"/><path d="M3 12h18M12 3c3 3 3 15 0 18M12 3c-3 3-3 15 0 18" fill="none" stroke="#a6a8ab" stroke-width="1.5"/></svg>
          </span>brightlaneinteriors.com
        </li>
      </ul>
    </div>

    <div class="appointment">
      <div class="field-row"><span>Name :</span><span class="field-line"></span></div>
      <div class="field-row">
        <span>Date :</span><span class="field-line"></span>
        <span>Time :</span><span class="field-line short"></span>
        <span class="field-suffix">AM/PM</span>
      </div>
    </div>

    <div class="partner"><span>Marlow Fenwick Gallery</span><span class="partner-dot"></span></div>

    <p class="locations">NORTHGATE | RIVERSIDE PARK | MAPLE HILL | WESTBROOK | LAKEVIEW</p>

    <ul class="social" aria-label="Social media">
      <li></li><li></li><li></li><li></li>
    </ul>
  </section>

</body>
</html>
```